Volbrey Inc Business Card

Looking to get an updated business card for a Contract Machining company (www.volbreyinc.example) - looking for a clean design the portrays the technical nature of the business - colors can follow the website design and be in any combination that makes sense (red black, white, metallic or silver) - logos attached for use also. Would like space for: Name, title, business phone (555 214-3086), cell phone , website (www.volbreyinc.example) - possibly QR code could be integrated for website (designer choice), business address - 418 Harlow Bend, Cedarvale, ST 48199 (cards will be for 4 employees, I will either need to modify a template or I can provide individual information)
Target Market(s)
Aerospace, defense and medical device manufacturing companies that need machining
Industry/Entity Type
Machining for aerospace, defense, medical
Contact Information for Business Card
Name, Title, Business Phone, Cell Phone, email, business website and business address
Look and feel

```html
<!DOCTYPE html>
<html lang="en">
<head>
<meta charset="utf-8">
<title>Volbrey Inc Business Card</title>
<link rel="stylesheet" href="https://fonts.googleapis.com/css2?family=Montserrat:wght@400;500;700&display=swap">
<style>
  :root {
    --brand-red: #b01e23;
    --ink: #151515;
    --card-white: #ffffff;
    --card-black: #151515;
    --backdrop: #e4e2e3;
  }
  * { box-sizing: border-box; margin: 0; padding: 0; }
  html, body {
    width: 1200px; height: 1108px; overflow: hidden;
    background: var(--backdrop);
    font-family: "Montserrat", sans-serif;
  }
  .canvas { position: relative; width: 1200px; height: 1108px; }
  .card { position: absolute; }
  .card-front { left: 229px; top: 56px; width: 754px; height: 461px; background: var(--card-white); }
  .card-back { left: 228px; top: 575px; width: 755px; height: 443px; background: var(--card-black); }

  .brand-disc { position: absolute; border-radius: 50%; background: var(--brand-red); }
  .front-disc { left: 218px; top: 172px; width: 130px; height: 130px; }
  .front-wordmark {
    position: absolute; left: 183px; top: 313px; width: 200px;
    text-align: center; color: var(--brand-red);
    font-weight: 700; font-size: 18px; letter-spacing: 0.3px;
  }
  .divider { position: absolute; left: 375px; top: 170px; width: 2px; height: 168px; background: var(--brand-red); }

  .contact-block { position: absolute; left: 394px; top: 166px; }
  .person-name { color: var(--brand-red); font-weight: 700; font-size: 28px; line-height: 1.1; }
  .person-title { color: var(--ink); font-size: 16px; font-weight: 500; margin-top: 2px; }
  .contact-list { list-style: none; margin-top: 20px; }
  .contact-list li {
    display: flex; align-items: center; gap: 8px;
    color: var(--ink); font-size: 17px; height: 25px;
  }
  .contact-list svg { width: 16px; height: 16px; fill: var(--brand-red); flex: none; }

  .address {
    position: absolute; left: 0; right: 0; top: 393px;
    text-align: center; color: var(--ink); font-size: 17px;
  }

  .back-disc { left: 276px; top: 67px; width: 250px; height: 250px; }
  .back-wordmark {
    position: absolute; left: 0; right: 0; top: 322px;
    text-align: center; color: var(--brand-red);
    font-weight: 700; font-size: 50px; letter-spacing: 1px;
  }
</style>
</head>
<body>
<main class="canvas">
  <section class="card card-front" aria-label="Business card front">
    <div class="brand-disc front-disc"></div>
    <div class="front-wordmark">VOLBREY INC</div>
    <div class="divider"></div>
    <div class="contact-block">
      <h1 class="person-name">Daniel Hart</h1>
      <p class="person-title">Owner</p>
      <ul class="contact-list">
        <li>
          <svg viewBox="0 0 24 24" aria-hidden="true"><path d="M6.6 10.8a15.1 15.1 0 0 0 6.6 6.6l2.2-2.2a1 1 0 0 1 1-.25 11.4 11.4 0 0 0 3.6.57 1 1 0 0 1 1 1V20a1 1 0 0 1-1 1A17 17 0 0 1 3 4a1 1 0 0 1 1-1h3.5a1 1 0 0 1 1 1c0 1.25.2 2.45.57 3.57a1 1 0 0 1-.25 1z"/></svg>
          <span>555 214-3086</span>
        </li>
        <li>
          <svg viewBox="0 0 24 24" aria-hidden="true"><path d="M3 9c0-3 4-5 9-5s9 2 9 5v2h-4V9H7v2H3zM6 12h12l2 8H4zm4 2v2h4v-2z"/></svg>
          <span>555 214-3086</span>
        </li>
        <li>
          <svg viewBox="0 0 24 24" aria-hidden="true"><path d="M2 5h20v14H2zm2 2v.5l8 5 8-5V7l-8 5z"/></svg>
          <span>info@volbreyinc.example</span>
        </li>
        <li>
          <svg viewBox="0 0 24 24" aria-hidden="true"><path d="M12 2a10 10 0 1 0 0 20 10 10 0 0 0 0-20zm-1 17.9A8 8 0 0 1 4.1 10L9 15v1a2 2 0 0 0 2 2zm6.9-2.5A2 2 0 0 0 16 16h-1v-3a1 1 0 0 0-1-1H8v-2h2a1 1 0 0 0 1-1V7h2a2 2 0 0 0 2-2v-.4a8 8 0 0 1 2.9 12.8z"/></svg>
          <span>www.volbreyinc.example</span>
        </li>
      </ul>
    </div>
    <p class="address">418 Harlow Bend, Cedarvale, ST 48199</p>
  </section>

  <section class="card card-back" aria-label="Business card back">
    <div class="brand-disc back-disc"></div>
    <div class="back-wordmark">VOLBREY</div>
  </section>
</main>
</body>
</html>
```